Coastal Gin Label Design

We are needing a nautical/coastal themed label for our upcoming gin release.

We have saltbush, cucumber, juniper, and quandong being used in this gin.

Name of the Gin; Harbour Moons

The logo attached is the company logo, but doesn't have to be used on the front of the label, ie it can just be the name Fernwhistle somewhere on the front.
Bottle specs attached as well so you can accurately represent the bottle- this bottle is also clear.

Target Market(s)

Women 25- 45

Font styles to use
Serif
Decorative

Colors
d5edf4
86cae7
33a6d7
86cfc6
cfeae6
ffffff
f6faec
ecf7fb
fefeff

Requirements
Must have
• Ocean/Coastal vibe to the label
Nice to have
• Blues,Whites clean and crisp
Should not have
• No generic word art look to it.
A dark mood

```html
<!DOCTYPE html>
<html lang="en">
<head>
<meta charset="utf-8">
<title>Saltmere Gin – Fernwhistle Distillery Label</title>
<link rel="stylesheet" href="https://fonts.googleapis.com/css2?family=Playfair+Display:wght@600;700&family=Libre+Baskerville&family=Josefin+Sans:wght@400;700&family=Oswald:wght@500&display=swap">
<style>
  :root {
    --canvas: #ffffff;
    --sea-light: #86cfc6;
    --sea-mid: #86cae7;
    --sea-deep: #33a6d7;
    --paper: #f4f4f2;
    --ink: #1d3558;
    --ink-soft: #3a3f48;
    --ink-dark: #2a2e35;
    --gold: #b99a55;
  }
  * { margin: 0; padding: 0; box-sizing: border-box; }
  html, body {
    width: 802px; height: 1200px; overflow: hidden;
    background: var(--canvas);
  }
  .label {
    position: absolute; left: 41px; top: 195px;
    width: 720px; height: 810px;
  }
  .label-art { position: absolute; inset: 0; }
  .medallion {
    position: absolute; left: 86px; top: 131px;
    width: 548px; height: 548px;
    text-align: center; color: var(--ink);
  }
  .brand-name {
    position: absolute; left: 0; right: 0; top: 104px;
    font-family: "Libre Baskerville", serif; font-weight: 400;
    font-size: 24px; line-height: 1; color: var(--ink);
  }
  .brand-sub {
    position: absolute; left: 0; right: 0; top: 146px;
    font-family: "Libre Baskerville", serif; font-size: 11px; color: var(--ink-soft);
  }
  .brand-origin {
    position: absolute; left: 0; right: 0; top: 166px;
    font-family: "Josefin Sans", sans-serif; font-size: 11px; color: var(--ink-soft);
  }
  .product-name {
    position: absolute; left: 0; right: 0; top: 212px;
    font-family: "Playfair Display", serif; font-weight: 700;
    font-size: 60px; line-height: 1; color: var(--ink);
  }
  .product-type {
    position: absolute; left: 300px; top: 282px;
    font-family: "Playfair Display", serif; font-weight: 600;
    font-size: 34px; line-height: 1; color: var(--ink);
  }
  .story {
    position: absolute; left: 70px; right: 70px; top: 356px;
    font-family: "Josefin Sans", sans-serif; font-size: 11.5px;
    line-height: 16.5px; color: var(--ink-soft);
  }
  .story strong { font-weight: 700; color: #1f2328; }
  .specs {
    position: absolute; left: 0; right: 0; top: 474px;
    font-family: "Oswald", sans-serif; font-weight: 500;
    font-size: 15px; color: var(--ink-dark); letter-spacing: 0.3px;
  }
  .specs-rule {
    position: absolute; left: 168px; width: 212px; top: 500px;
    height: 1px; background: var(--ink-dark);
  }
  .specs-drinks {
    position: absolute; left: 0; right: 0; top: 504px;
    font-family: "Oswald", sans-serif; font-weight: 500;
    font-size: 15px; color: var(--ink-dark); letter-spacing: 0.3px;
  }
</style>
</head>
<body>
  <div class="label">
    <svg class="label-art" width="720" height="810" viewBox="0 0 720 810">
      <defs>
        <linearGradient id="sea-wash" x1="0" y1="0" x2="0.3" y2="1">
          <stop offset="0" stop-color="#8fd3cf"/>
          <stop offset="0.45" stop-color="#86cae7"/>
          <stop offset="1" stop-color="#3fa4d6"/>
        </linearGradient>
        <linearGradient id="gold-band" x1="0" y1="0" x2="1" y2="1">
          <stop offset="0" stop-color="#b99a55"/>
          <stop offset="0.5" stop-color="#dcc68e"/>
          <stop offset="1" stop-color="#a8884a"/>
        </linearGradient>
      </defs>
      <rect width="720" height="810" fill="url(#sea-wash)" role="img" aria-label="Engraved seashells and seaweed over a turquoise-to-blue ocean wash"/>
      <circle cx="360" cy="405" r="292" fill="none" stroke="url(#gold-band)" stroke-width="34" stroke-opacity="0.75" role="img" aria-label="Gold foil wave-pattern ring"/>
      <circle cx="360" cy="405" r="274" fill="#f4f4f2"/>
      <circle cx="360" cy="405" r="274" fill="none" stroke="#b99a55" stroke-width="1.5"/>
    </svg>

    <div class="medallion">
      <div class="brand-name">Fernwhistle</div>
      <div class="brand-sub">Distillery, WA</div>
      <div class="brand-origin">Handcrafted in Australia</div>

      <div class="product-name">Saltmere</div>
      <div class="product-type">Gin</div>

      <p class="story">
        <strong>Made in Coralby, Western Australia<br>
        with 100% Australian made and Owned Fermentables.</strong><br>
        Double distilled with botanicals within our vapour basket<br>
        foraged from the local areas and the Saltmere itself<br>
        to represent the Saltmere islands in a bottle.<br>
        Drink with friends and consume responsibly.
      </p>

      <div class="specs">40% ABV | 80 PROOF | 500 ML</div>
      <div class="specs-rule"></div>
      <div class="specs-drinks">APPROX. 16 STD DRINKS</div>
    </div>
  </div>
</body>
</html>
```